Using attached logo that has been created

Business card with logo that's attached. Maybe with water or the cartoon van in background. Looking for it to not be so plain and not too white.
Information to include;
Rodney Ashcombe
(555) 218-7730
Info@bramleypipeworks.example
www.bramleypipeworks.example
License # 4627195
Looking forward to the designs u come up with.
Thank you!
-Delphine
Target Market(s)
Plumbing
Industry/Entity Type
Plumbing
Contact Information for Business Card
Listed above

```html
<!DOCTYPE html>
<html lang="en">
<head>
<meta charset="utf-8">
<title>Bramley Pipeworks – Business Card</title>
<link rel="stylesheet" href="https://fonts.googleapis.com/css2?family=Open+Sans:wght@400;600;700&display=swap">
<style>
  :root {
    --page-bg: #e9e9eb;
    --card-white: #ffffff;
    --card-dark: #1d1e21;
    --card-dark-2: #2a2b2f;
    --brand-blue: #1c5bb8;
    --brand-yellow: #f4b41a;
    --ink: #222326;
    --rule: #8c8c90;
    --art-blue: #2f6fd0;
    --art-tan: #b89a6a;
  }
  * { box-sizing: border-box; margin: 0; padding: 0; }
  html, body { width: 1200px; height: 1108px; overflow: hidden; }
  body {
    background: var(--page-bg);
    font-family: "Open Sans", Arial, sans-serif;
    position: relative;
  }
  .card {
    position: absolute;
    top: 194px;
    width: 420px;
    height: 720px;
    border-radius: 26px;
    box-shadow: 0 18px 40px rgba(0,0,0,.18);
    overflow: hidden;
  }
  .card--front { left: 150px; background: var(--card-white); }
  .card--back  { left: 630px; background: var(--card-dark); }

  .mascot-art {
    position: absolute;
    left: 95px; top: 60px;
    width: 230px; height: 250px;
    border-radius: 20px;
    background: linear-gradient(180deg, #d9e4f5 0%, var(--art-blue) 45%, var(--art-tan) 100%);
  }
  .logo-name {
    position: absolute;
    left: 0; right: 0; top: 322px;
    text-align: center;
    font-weight: 700;
    font-size: 36px;
    color: var(--brand-blue);
    letter-spacing: .5px;
  }
  .person-name {
    position: absolute;
    left: 0; right: 0; top: 410px;
    text-align: center;
    font-weight: 600;
    font-size: 30px;
    color: var(--brand-blue);
    letter-spacing: .5px;
  }
  .contact-icons {
    position: absolute;
    left: 40px; right: 40px; top: 470px;
    display: flex; align-items: center; gap: 10px;
  }
  .contact-icons .rule { flex: 1; height: 1px; background: var(--rule); }
  .icon-box {
    width: 38px; height: 38px; border-radius: 7px;
    background: var(--brand-blue);
    display: flex; align-items: center; justify-content: center;
  }
  .contact-list {
    position: absolute;
    left: 0; right: 0; top: 522px;
    text-align: center;
    font-size: 21px;
    line-height: 31px;
    color: var(--ink);
  }
  .contact-list .domain { color: var(--brand-blue); }
  .divider {
    position: absolute; left: 50px; right: 50px; top: 630px;
    height: 1px; background: var(--rule);
  }
  .license {
    position: absolute; left: 0; right: 0; top: 648px;
    text-align: center; font-size: 22px; color: var(--brand-blue);
  }
  .license .number { color: var(--brand-yellow); }

  .back-texture {
    position: absolute; inset: 0;
    background: linear-gradient(160deg, var(--card-dark-2) 0%, var(--card-dark) 55%, #151618 100%);
  }
  .back-name {
    position: absolute;
    left: 0; right: 0; top: 500px;
    text-align: center;
    font-weight: 700;
    font-size: 32px;
    color: var(--brand-blue);
  }
</style>
</head>
<body>
  <section class="card card--front">
    <div class="mascot-art" role="img" aria-label="Cartoon mascot of a plumber holding a pipe wrench and a circular saw"></div>
    <div class="logo-name">Bramley Pipeworks</div>
    <h1 class="person-name">RODNEY ASHCOMBE</h1>
    <div class="contact-icons">
      <span class="rule"></span>
      <span class="icon-box">
        <svg width="22" height="22" viewBox="0 0 24 24" fill="#fff"><path d="M6.6 10.8a15 15 0 0 0 6.6 6.6l2.2-2.2c.3-.3.7-.4 1-.2 1.1.4 2.3.6 3.6.6.6 0 1 .4 1 1V20c0 .6-.4 1-1 1A17 17 0 0 1 3 4c0-.6.4-1 1-1h3.5c.6 0 1 .4 1 1 0 1.3.2 2.5.6 3.6.1.3 0 .7-.2 1z"/></svg>
      </span>
      <span class="icon-box">
        <svg width="22" height="22" viewBox="0 0 24 24" fill="none" stroke="#fff" stroke-width="2"><rect x="3" y="5" width="18" height="14" rx="1"/><path d="M3 6l9 7 9-7"/></svg>
      </span>
      <span class="icon-box">
        <svg width="22" height="22" viewBox="0 0 24 24" fill="none" stroke="#fff" stroke-width="1.8"><circle cx="12" cy="12" r="9"/><path d="M3 12h18M12 3c3 3 3 15 0 18M12 3c-3 3-3 15 0 18"/></svg>
      </span>
      <span class="rule"></span>
    </div>
    <address class="contact-list" style="font-style:normal">
      (555) 218-7730<br>
      Info@bramleypipeworks.example<br>
      www.<span class="domain">bramleypipeworks</span>.example
    </address>
    <div class="divider"></div>
    <p class="license">License <span class="number"># 4627195</span></p>
  </section>

  <section class="card card--back">
    <div class="back-texture" role="img" aria-label="Faint repeating pattern of the company wordmark on dark background"></div>
    <div class="back-name">Bramley Pipeworks</div>
  </section>
</body>
</html>
```